swimming pool Leak Detection Brochure

I would Like to create a pool leak detection brochure

Target Market(s)

High end Clients with inground swimming pools

Industry/Entity Type

Pool Service

Font styles to use
Other font styles liked:
• Im open to suggestions but using my website for ideas is suggested

Colors

Designer to choose colors to be used in the design.

Requirements
Must have
• Do you Have a Leak??
• Figuring out when your pool has a leak can be tough. Environmental factors do play a role in the water level, and just because your pool’s water is lower than normal does not mean it has a leak. Wind, humidity, and sun exposure all impact your rate of evaporation.
• Warning Signs of a Leak in Your Pool
• Your pool, fountain, or spa loses more than 1/4 an inch of water a day
• There are cracks in or around the pool decking
• You need to add water more than once a week
• Grass around the area is soggy
• Your pool deck is sinking or lifting
Nice to have
• PREPARING FOR A LEAK TEST
• To ensure you receive an accurate leak detection test, it is required that you have the pool vacuumed and cleaned beforehand. Dirt and debris in the pool can make it difficult to spot even large leaks. Likewise, the water should be as clear as possible. If your water is green it means mildew, algae, or fungi has infested it. Not only does this make it impossible to test for leaks, but it’s dangerous for our health. Finally our pool should be full to the normal level - we can’t find a leak that is not leaking! After your test, you will be confident knowing you have a pool/fountain/spa that is free of leaks or the Leak has been found and can be repaired Properly.

```html
<!DOCTYPE html>
<html lang="en">
<head>
<meta charset="utf-8">
<title>Harbor Pool Works – Leak Detection Brochure</title>
<link rel="stylesheet" href="https://fonts.googleapis.com/css2?family=Open+Sans:wght@400;600;700;800&family=Permanent+Marker&family=Lora:wght@400;500&display=swap">
<style>
:root{
  --blue-deep:#0c3c8c;
  --blue:#1a63c4;
  --blue-bright:#2a8be0;
  --sky:#62b6f0;
  --orange:#e8742a;
  --orange-deep:#cf5b17;
  --ink:#222831;
  --text:#4a4f57;
  --paper:#ffffff;
  --stage:#e6e8eb;
  --star:#f5a623;
  --marker:"Permanent Marker", cursive;
  --sans:"Open Sans", Arial, sans-serif;
  --serif:"Lora", Georgia, serif;
}
*{box-sizing:border-box;margin:0;padding:0}
html,body{width:1200px;height:2452px;overflow:hidden}
body{background:var(--stage);font-family:var(--sans);color:var(--text);position:relative}

.spread{position:absolute;left:60px;width:1080px;height:765px;display:flex;box-shadow:0 10px 30px rgba(0,0,0,.18)}
.spread--cover{top:40px}
.spread--leak{top:843px}
.spread--renovation{top:1646px}
.page{position:relative;width:540px;height:765px;overflow:hidden;background:var(--paper)}
.page + .page{box-shadow:inset 10px 0 14px -10px rgba(0,0,0,.18)}

.photo{position:absolute}
.photo--round{border-radius:50%;border:5px solid #fff;box-shadow:0 3px 10px rgba(0,0,0,.25)}

/* ---------- Back cover ---------- */
.back-cover{background:linear-gradient(160deg,var(--blue) 0%,var(--blue-deep) 100%)}
.back-cover__photo{left:0;top:0;width:540px;height:360px;background:linear-gradient(135deg,#eef4fa 0%,#a9cbe9 35%,#3a7fd0 75%,var(--blue) 100%)}
.back-cover__curves{position:absolute;left:0;top:0}
.testimonial{position:absolute;left:250px;width:260px;color:#fff}
.testimonial__quote{position:absolute;left:-34px;top:-6px;font-family:var(--serif);font-size:46px;line-height:1;color:#fff;opacity:.9}
.testimonial__stars{color:var(--star);font-size:13px;letter-spacing:2px;text-align:right}
.testimonial__text{font-size:9.5px;line-height:1.5;margin-top:4px}
.testimonial__name{font-family:var(--serif);font-size:16px;font-style:italic;text-align:center;margin-top:6px}
.testimonial--one{top:28px}
.testimonial--two{top:152px}
.badges{position:absolute;left:30px;top:292px;width:480px;height:80px}
.badge{position:absolute;width:68px;height:68px;border-radius:50%;background:#fff;border:4px solid #cfe0f3;box-shadow:0 3px 8px rgba(0,0,0,.3)}
.badge::after{content:"";position:absolute;inset:10px;border-radius:50%;background:var(--sky);opacity:.55}
.badge--member{position:absolute;left:60px;top:570px;width:104px;height:104px;background:#fff;border-radius:4px;box-shadow:0 3px 8px rgba(0,0,0,.3)}
.badge--member::after{content:"";position:absolute;left:22px;top:18px;width:60px;height:44px;border-radius:50%;background:var(--sky);opacity:.55}
.contact{position:absolute;left:250px;top:430px;color:#fff}
.contact__title{font-weight:800;font-size:17px;letter-spacing:.5px;margin-bottom:8px}
.contact__line{font-size:12px;line-height:1.55}
.contact__email{font-size:12px;margin-top:8px;display:flex;align-items:center;gap:8px}
.contact__phone{margin-top:10px;display:inline-block;border:2px solid #fff;border-radius:22px;padding:4px 22px 4px 40px;font-weight:800;font-size:24px;position:relative}
.contact__phone svg{position:absolute;left:10px;top:9px}
.contact__web{font-size:14px;margin-top:14px;display:flex;align-items:center;gap:8px}

/* ---------- Front cover ---------- */
.front-cover{background:linear-gradient(170deg,var(--blue-bright) 0%,var(--blue) 55%,var(--blue-deep) 100%)}
.front-cover__photo{left:0;top:0;width:540px;height:520px;background:linear-gradient(180deg,#8fc7f0 0%,#6fae73 24%,#3f8fd8 46%,#1f6fd0 70%,#1457b8 100%)}
.front-cover__waves{position:absolute;left:0;top:0}
.brand{position:absolute;left:306px;top:358px;width:150px;height:150px;border-radius:50%;background:#fff;display:flex;align-items:center;justify-content:center;text-align:center;box-shadow:0 4px 14px rgba(0,0,0,.3)}
.brand__name{font-family:var(--sans);font-weight:800;font-size:20px;line-height:1.15;color:var(--blue-deep)}
.front-cover__title{position:absolute;left:80px;top:560px;font-family:var(--serif);font-size:30px;line-height:1.3;color:#fff}
.front-cover__web{position:absolute;right:28px;top:528px;color:#fff;font-size:14px;display:flex;align-items:center;gap:6px}

/* ---------- Interior shared ---------- */
.heading-marker{font-family:var(--marker);font-size:26px;line-height:1.15;color:var(--ink);letter-spacing:.5px;white-space:nowrap}
.heading-marker em{font-style:normal;color:var(--blue-bright)}
.heading-rule{height:2px;background:var(--blue-bright);margin:8px 0 12px}
.body-copy{font-size:10.5px;line-height:1.55;color:var(--text)}
.ticks{list-style:none;margin-top:6px}
.ticks li{font-size:10.5px;line-height:1.6;padding-left:18px;position:relative}
.ticks li::before{content:"✔";position:absolute;left:0;top:0;color:var(--orange);font-size:11px}
.ticks--bold li{font-weight:700;color:var(--ink)}
.section-title{font-weight:800;font-size:14px;letter-spacing:.3px;text-transform:uppercase;color:var(--orange)}
.section-title--blue{color:var(--blue)}
.bottom-band{position:absolute;left:0;bottom:0}
.band-text{position:absolute;color:#fff;display:flex;align-items:center;gap:8px;white-space:nowrap;z-index:2}

/* ---------- Leak page ---------- */
.leak{padding:36px 40px 0 44px}
.leak__sub{font-weight:700;font-size:11px;color:var(--ink);margin-top:6px}
.leak__prep{margin-top:16px}
.brand-row{position:absolute;left:44px;top:494px;width:220px;height:70px}
.brand-row span{position:absolute;height:16px;border-radius:3px;background:#b7bcc4}
.leak__phone{left:30px;bottom:44px;font-weight:800;font-size:24px}
.leak__equipment{left:300px;top:560px;width:170px;height:170px;background:radial-gradient(circle at 45% 45%,#e7e9ec 0%,#9aa3ad 55%,#4b5560 100%)}

/* ---------- Maintenance page ---------- */
.maint{padding:44px 44px 0 40px}
.maint .heading-marker{font-size:26px;color:var(--blue-bright)}
.maint__company{font-weight:800;font-size:13px;color:var(--ink);margin:12px 0 8px}
.maint__company span{font-weight:600;color:var(--text)}
.maint__benefits{font-weight:800;font-size:14px;color:var(--ink);margin:14px 0 6px}
.maint__guarantee{font-weight:800;font-size:12px;line-height:1.45;color:var(--orange);margin-top:12px}
.maint__guarantee span{color:var(--blue)}
.maint__duck{left:60px;top:555px;width:150px;height:150px;background:radial-gradient(circle at 50% 45%,#f7d34a 0%,#5fb3e8 45%,#1f75c9 100%)}
.maint__pool{left:290px;top:520px;width:180px;height:180px;background:linear-gradient(180deg,#d9ecf8 0%,#7cc0ea 50%,#2f84d0 100%)}
.maint__web{right:30px;bottom:16px;font-size:13px}

/* ---------- Renovation pages ---------- */
.reno{padding:34px 36px 0 40px}
.reno__block{margin-top:12px}
.reno__types{font-weight:800;font-size:12px;color:var(--ink);margin-top:6px}
.reno__split{display:flex;gap:18px}
.reno__split .ticks{flex:0 0 auto}
.reno__deck1{left:320px;top:300px;width:110px;height:110px;background:linear-gradient(135deg,#c8c2b8,#7b7b78)}
.reno__deck2{left:398px;top:380px;width:100px;height:100px;background:linear-gradient(135deg,#b9b3a6,#5d6670)}
.reno__struct1{left:250px;top:575px;width:105px;height:105px;background:linear-gradient(135deg,#d6d2c8,#8d8a84)}
.reno__struct2{left:365px;top:600px;width:120px;height:120px;background:linear-gradient(135deg,#c4c0b6,#6e7074)}
.reno__web{left:34px;bottom:120px;font-size:13px}
.reno-right{padding:44px 40px 0 36px}
.reno-right .section-title{text-align:left}
.reno__coping{left:345px;top:335px;width:100px;height:100px;background:linear-gradient(135deg,#dfeaf1,#5fa6d6)}
.reno__tile{left:420px;top:400px;width:100px;height:100px;background:linear-gradient(135deg,#9cc7e8,#1b63b2)}
.reno__filter1{left:90px;top:638px;width:100px;height:100px;background:linear-gradient(135deg,#d5e6f1,#4f8fc4)}
.reno__filter2{left:200px;top:625px;width:115px;height:115px;background:linear-gradient(135deg,#e3e5e8,#8e98a3)}
.reno__filter3{left:330px;top:605px;width:130px;height:130px;background:linear-gradient(135deg,#c9e3f5,#3d8ad1)}
</style>
</head>
<body>

<section class="spread spread--cover">
  <div class="page back-cover">
    <div class="photo back-cover__photo" role="img" aria-label="Photo of an automatic pool cleaner in clear blue water"></div>
    <svg class="back-cover__curves" width="540" height="765" viewBox="0 0 540 765">
      <path d="M0,330 C150,300 360,380 540,300 L540,765 L0,765 Z" fill="#1656b2" opacity=".92"/>
      <path d="M0,340 C160,310 360,392 540,312" fill="none" stroke="#fff" stroke-width="3" opacity=".8"/>
      <path d="M0,360 C170,330 360,410 540,332" fill="none" stroke="#7fc1f2" stroke-width="2" opacity=".6"/>
      <path d="M0,700 C180,640 360,740 540,660" fill="none" stroke="#fff" stroke-width="2" opacity=".35"/>
    </svg>
    <div class="testimonial testimonial--one">
      <span class="testimonial__quote">“</span>
      <div class="testimonial__stars">★★★★★</div>
      <p class="testimonial__text">I am so happy I found this company! After years of guessing, they located our leak in one visit and fixed it the same week. Honest, careful and always on time. Highly recommended.</p>
      <p class="testimonial__name">Delia R.</p>
    </div>
    <div class="testimonial testimonial--two">
      <span class="testimonial__quote">“</span>
      <div class="testimonial__stars">★★★★★</div>
      <p class="testimonial__text">I was a longtime customer of a bigger outfit, but this crew is in a league of their own. They explain every step, keep the yard clean and the price was fair. Our pool has never looked better.</p>
      <p class="testimonial__name">Tomas K.</p>
    </div>
    <div class="badges">
      <span class="badge" style="left:0;top:40px"></span>
      <span class="badge" style="left:110px;top:0"></span>
      <span class="badge" style="left:220px;top:-10px"></span>
      <span class="badge" style="left:340px;top:-6px"></span>
    </div>
    <div class="badge--member"></div>
    <div class="contact">
      <p class="contact__title">CONTACT US</p>
      <p class="contact__line">Harbor Pool Works</p>
      <p class="contact__line">RI REG # 40917</p>
      <p class="contact__line">CT License # SP1-PLM 0377152</p>
      <p class="contact__email">
        <svg width="14" height="10" viewBox="0 0 14 10"><rect x=".5" y=".5" width="13" height="9" fill="none" stroke="#fff"/><path d="M.5,.5 L7,6 L13.5,.5" fill="none" stroke="#fff"/></svg>
        sam@harborpoolworks.com
      </p>
      <p class="contact__phone">
        <svg width="18" height="18" viewBox="0 0 24 24"><path d="M6.6 10.8a15 15 0 0 0 6.6 6.6l2.2-2.2a1 1 0 0 1 1-.25 11.4 11.4 0 0 0 3.6.57 1 1 0 0 1 1 1V20a1 1 0 0 1-1 1A17 17 0 0 1 3 4a1 1 0 0 1 1-1h3.5a1 1 0 0 1 1 1c0 1.250.2 2.450.57 3.57a1 1 0 0 1-.25 1z" fill="#fff"/></svg>
        555-014-2290
      </p>
      <p class="contact__web">
        <svg width="14" height="14" viewBox="0 0 14 14"><circle cx="7" cy="7" r="6.3" fill="none" stroke="#fff"/><ellipse cx="7" cy="7" rx="2.8" ry="6.3" fill="none" stroke="#fff"/><line x1=".7" y1="7" x2="13.3" y2="7" stroke="#fff"/></svg>
        www.harborpoolworks.com
      </p>
    </div>
  </div>

  <div class="page front-cover">
    <div class="photo front-cover__photo" role="img" aria-label="Photo of a luxury resort-style pool with palm trees and swimmers"></div>
    <svg class="front-cover__waves" width="540" height="765" viewBox="0 0 540 765">
      <path d="M0,470 C160,430 330,520 540,440 L540,765 L0,765 Z" fill="#1a63c4"/>
      <path d="M0,480 C160,440 330,530 540,450" fill="none" stroke="#fff" stroke-width="4"/>
      <path d="M0,500 C160,462 330,548 540,472" fill="none" stroke="#7fc1f2" stroke-width="2"/>
      <path d="M0,740 C200,690 380,760 540,700 L540,765 L0,765 Z" fill="#0c3c8c" opacity=".6"/>
    </svg>
    <div class="brand"><span class="brand__name">Harbor<br>Pool Works</span></div>
    <h1 class="front-cover__title">Dive Into<br>Professional Pool<br>Service &amp; Repair</h1>
    <p class="front-cover__web">
      <svg width="13" height="13" viewBox="0 0 14 14"><circle cx="7" cy="7" r="6.3" fill="none" stroke="#fff"/><ellipse cx="7" cy="7" rx="2.8" ry="6.3" fill="none" stroke="#fff"/><line x1=".7" y1="7" x2="13.3" y2="7" stroke="#fff"/></svg>
      www.harborpoolworks.com
    </p>
  </div>
</section>

<section class="spread spread--leak">
  <div class="page leak">
    <h2 class="heading-marker">DO YOU HAVE A <em>LEAK??</em></h2>
    <div class="heading-rule"></div>
    <p class="body-copy">Figuring out when your pool has a leak can be tough. Environmental factors do play a role in the water level, and just because your pool’s water is lower than normal does not mean it has a leak. Wind, humidity, and sun exposure all impact your rate of evaporation.</p>
    <p class="leak__sub">Warning Signs of a Leak in Your Pool</p>
    <ul class="ticks">
      <li>Your pool, fountain, or spa loses more than 1/4 an inch of water a day</li>
      <li>There are cracks in or around the pool decking</li>
      <li>You need to add water more than once a week</li>
      <li>Grass around the area is soggy</li>
      <li>Your pool deck is sinking or lifting</li>
    </ul>
    <div class="leak__prep">
      <h2 class="heading-marker">PREPARING FOR A <em>LEAK TEST?</em></h2>
      <div class="heading-rule"></div>
      <p class="body-copy">To ensure you receive an accurate leak detection test, it is required that you have the pool vacuumed and cleaned beforehand. Dirt and debris in the pool can make it difficult to spot even large leaks. Likewise, the water should be as clear as possible. If your water is green it means mildew, algae, or fungi has infested it. Not only does this make it impossible to test for leaks, but it’s dangerous for our health. Finally our pool should be full to the normal level - we can’t find a leak that is not leaking! After your test, you will be confident knowing you have a pool/fountain/spa that is free of leaks or the Leak has been found and can be repaired Properly.</p>
    </div>
    <div class="brand-row" aria-hidden="true">
      <span style="left:0;top:0;width:70px"></span>
      <span style="left:84px;top:0;width:54px"></span>
      <span style="left:150px;top:0;width:60px"></span>
      <span style="left:0;top:24px;width:80px"></span>
      <span style="left:120px;top:24px;width:90px"></span>
      <span style="left:20px;top:48px;width:60px"></span>
      <span style="left:130px;top:48px;width:70px"></span>
    </div>
    <svg class="bottom-band" width="540" height="220" viewBox="0 0 540 220">
      <path d="M0,90 C160,40 360,150 540,70 L540,220 L0,220 Z" fill="#e8742a"/>
      <path d="M0,78 C160,28 360,138 540,58" fill="none" stroke="#d3d8de" stroke-width="5"/>
      <path d="M0,100 C160,50 360,160 540,80" fill="none" stroke="#fff" stroke-width="2"/>
    </svg>
    <p class="band-text leak__phone">
      <svg width="22" height="22" viewBox="0 0 24 24"><circle cx="12" cy="12" r="11" fill="none" stroke="#fff" stroke-width="1.5"/><path d="M8.6 10.6a8 8 0 0 0 3.8 3.8l1.3-1.3a.6.6 0 0 1 .6-.15 6.5 6.5 0 0 0 2 .33.6.6 0 0 1 .6.6v2a.6.6 0 0 1-.6.6A9.9 9.9 0 0 1 6.4 6.6a.6.6 0 0 1 .6-.6h2a.6.6 0 0 1 .6.6c0 .7.1 1.4.33 2a.6.6 0 0 1-.15.6z" fill="#fff"/></svg>
      555-014-2290
    </p>
    <div class="photo photo--round leak__equipment" role="img" aria-label="Photo of leak detection equipment and tools"></div>
  </div>

  <div class="page maint">
    <h2 class="heading-marker">POOL MAINTENANCE,<br>CLEANING, &amp; REPAIRS IN RI</h2>
    <p class="maint__company">HARBOR POOL WORKS <span>RI, MA, CT</span></p>
    <p class="body-copy">Serving Massachusetts, Rhode Island, including Block Island and Connecticut, Harbor Pool Works stands ready to provide exceptional pool service to homeowners. Whether it’s a seasonal opening, a weekly cleaning or repair of a hidden leak, our trained staff keeps your pool safe, clear and inviting all year long.</p>
    <p class="maint__benefits">Benefits of Harbor Pool Works</p>
    <p class="body-copy">As a family owned and operated small business, the founder of Harbor Pool Works treats every backyard like his own. We take the time to listen, explain our findings and respect your property, so you always know what to expect from your visit.</p>
    <p class="body-copy" style="margin-top:8px">We have always strived to provide a high level of pool service at the initial stages of a project as well as after the job is complete, so we are always ready to answer questions and help keep your pool running smoothly.</p>
    <p class="maint__guarantee">Your satisfaction is GUARANTEED.<br><span>For Pool Repair, Maintenance, and Cleaning<br>Call Harbor Pool Works TODAY!!!</span></p>
    <svg class="bottom-band" width="540" height="240" viewBox="0 0 540 240">
      <path d="M0,120 C180,170 360,40 540,60 L540,240 L0,240 Z" fill="#e8742a"/>
      <path d="M0,108 C180,158 360,28 540,48" fill="none" stroke="#d3d8de" stroke-width="5"/>
      <path d="M0,130 C180,180 360,50 540,70" fill="none" stroke="#fff" stroke-width="2"/>
    </svg>
    <div class="photo photo--round maint__duck" role="img" aria-label="Photo of a rubber duck floating in a blue pool"></div>
    <div class="photo photo--round maint__pool" role="img" aria-label="Photo of a technician cleaning a pool"></div>
    <p class="band-text maint__web">
      <svg width="13" height="13" viewBox="0 0 14 14"><circle cx="7" cy="7" r="6.3" fill="none" stroke="#fff"/><ellipse cx="7" cy="7" rx="2.8" ry="6.3" fill="none" stroke="#fff"/><line x1=".7" y1="7" x2="13.3" y2="7" stroke="#fff"/></svg>
      www.harborpoolworks.com
    </p>
  </div>
</section>

<section class="spread spread--renovation">
  <div class="page reno">
    <h2 class="heading-marker">RENOVATION</h2>
    <div class="heading-rule"></div>
    <p class="body-copy">A great looking pool starts with a solid plan. From a simple refresh to a full rebuild, our renovation team handles design, demolition and finishing so your backyard becomes a place you love to spend time again.</p>
    <div class="reno__block">
      <h3 class="section-title">Pool Decking Removal and Renovation</h3>
      <div class="heading-rule"></div>
      <p class="body-copy">Old or cracked decking can be unsafe and unsightly. We remove worn surfaces and install durable new materials that suit your style.</p>
      <p class="reno__types">TYPES OF DECKING:</p>
      <ul class="ticks ticks--bold">
        <li>Stamped Concrete</li>
        <li>Pavers</li>
        <li>Exposed Aggregate</li>
        <li>Blue Stone</li>
        <li>Plain Concrete</li>
      </ul>
    </div>
    <div class="reno__block">
      <h3 class="section-title">Structural Repair</h3>
      <div class="heading-rule"></div>
      <p class="body-copy" style="width:280px">Shifting soil and age can weaken pool walls and steps. We repair damage at the source to protect your investment for years.</p>
      <div class="reno__split">
        <ul class="ticks ticks--bold">
          <li>Wall Repair</li>
          <li>Pool Depth Alterations</li>
          <li>Crack Repair &amp; Injection</li>
        </ul>
        <ul class="ticks ticks--bold">
          <li>Step Replacement</li>
          <li>Interior Walls</li>
        </ul>
      </div>
    </div>
    <div class="photo photo--round reno__deck1" role="img" aria-label="Photo of pool decking being removed"></div>
    <div class="photo photo--round reno__deck2" role="img" aria-label="Photo of new paver decking around a pool"></div>
    <svg class="bottom-band" width="540" height="210" viewBox="0 0 540 210">
      <path d="M0,40 C180,10 360,140 540,120 L540,210 L0,210 Z" fill="#e8742a"/>
      <path d="M0,28 C180,-2 360,128 540,108" fill="none" stroke="#d3d8de" stroke-width="5"/>
      <path d="M0,50 C180,20 360,150 540,130" fill="none" stroke="#fff" stroke-width="2"/>
    </svg>
    <div class="photo photo--round reno__struct1" role="img" aria-label="Photo of a pool wall under structural repair"></div>
    <div class="photo photo--round reno__struct2" role="img" aria-label="Photo of an empty pool during renovation"></div>
    <p class="band-text reno__web">
      <svg width="13" height="13" viewBox="0 0 14 14"><circle cx="7" cy="7" r="6.3" fill="none" stroke="#fff"/><ellipse cx="7" cy="7" rx="2.8" ry="6.3" fill="none" stroke="#fff"/><line x1=".7" y1="7" x2="13.3" y2="7" stroke="#fff"/></svg>
      www.harborpoolworks.com
    </p>
  </div>

  <div class="page reno-right">
    <h3 class="section-title">Plumbing Updates and Upgrades</h3>
    <div class="heading-rule"></div>
    <p class="body-copy">Outdated plumbing wastes water and energy. We upgrade lines and fittings to improve flow, efficiency and reliability.</p>
    <ul class="ticks ticks--bold">
      <li>Inlets</li>
      <li>Skimmer Replacements</li>
      <li>Main Drain Replacement</li>
      <li>Automatic Pool Cleaners</li>
    </ul>
    <div class="reno__block">
      <h3 class="section-title">Pool Coping Removal &amp; Replacement</h3>
      <div class="heading-rule"></div>
      <p class="body-copy">Coping frames your pool and protects its edge. We replace loose or damaged stones with lasting, elegant materials.</p>
      <p class="reno__types">TYPES OF POOL COPING:</p>
      <ul class="ticks ticks--bold">
        <li>Bullnose Brick</li>
        <li>Cantilever</li>
        <li>White Coping</li>
        <li>Blue Stone</li>
        <li>Cantilever Poured Band</li>
      </ul>
    </div>
    <div class="reno__block">
      <h3 class="section-title">Tile Removal &amp; Replacement</h3>
      <div class="heading-rule"></div>
      <p class="body-copy">Cracked or faded tile is replaced with fresh, long lasting finishes.</p>
      <ul class="ticks ticks--bold" style="margin-top:8px">
        <li class="section-title section-title--blue" style="font-size:13px">Pool Interior Resurfacing / Replastering</li>
        <li class="section-title" style="font-size:13px">Filter System and Equipment<br>Upgrades / Replacement:</li>
      </ul>
    </div>
    <div class="photo photo--round reno__coping" role="img" aria-label="Photo of new stone pool coping"></div>
    <div class="photo photo--round reno__tile" role="img" aria-label="Photo of blue pool tile"></div>
    <svg class="bottom-band" width="540" height="180" viewBox="0 0 540 180">
      <path d="M0,110 C180,140 360,30 540,20 L540,180 L0,180 Z" fill="#e8742a"/>
      <path d="M0,98 C180,128 360,18 540,8" fill="none" stroke="#d3d8de" stroke-width="5"/>
      <path d="M0,120 C180,150 360,40 540,30" fill="none" stroke="#fff" stroke-width="2"/>
    </svg>
    <div class="photo photo--round reno__filter1" role="img" aria-label="Photo of a refinished pool interior"></div>
    <div class="photo photo--round reno__filter2" role="img" aria-label="Photo of pool filter and pump equipment"></div>
    <div class="photo photo--round reno__filter3" role="img" aria-label="Photo of a technician resurfacing a pool"></div>
  </div>
</section>

</body>
</html>
```